Kestrelbrook Student Accomodation needs a business card design

Hi Guys,

We are a Student Accommodation company in Australia. We already have a logo which I will submit.

I will require the design of the business cards from you.

I am after something that looks clean, modern and that people feel interested and actually want to contact us.

We would like to see designs that are innovative.

On the business cards I will require to have:

Employee Name
Position
Phone number
Email
Facebook page

I hope you can help me with this project guys as I have heard really good things from you.

```html
<!DOCTYPE html>
<html lang="en">
<head>
<meta charset="utf-8">
<title>Kestrelbrook Student Accomodation – Business Card</title>
<link href="https://fonts.googleapis.com/css2?family=Exo+2:wght@300;400;700&display=swap" rel="stylesheet">
<style>
  :root{
    --bg:#e9e7e3;
    --card:#ffffff;
    --card-shade:#ececec;
    --green:#1e9a2a;
    --yellow:#f2b01e;
    --ink:#3a3a3a;
    --ink-soft:#6a6a6a;
  }
  *{box-sizing:border-box;margin:0;padding:0}
  html,body{width:1200px;height:828px;overflow:hidden}
  body{
    background:var(--bg);
    font-family:"Exo 2",Arial,sans-serif;
    color:var(--ink);
    display:flex;align-items:center;justify-content:center;gap:44px;
  }
  .card{
    position:relative;width:530px;height:303px;
    background:radial-gradient(ellipse at 40% 40%,var(--card) 55%,var(--card-shade) 100%);
    box-shadow:0 6px 18px rgba(0,0,0,.18);
    overflow:hidden;
  }
  .brand{display:flex;align-items:center;gap:10px}
  .brand-mark{width:26px;height:26px;background:var(--yellow)}
  .brand-name{font-weight:700;color:var(--green);font-size:26px;letter-spacing:.5px;text-transform:uppercase}
  .card-front .brand{position:absolute;left:50%;top:50%;transform:translate(-50%,-50%)}
  .card-back .brand{position:absolute;left:44px;top:92px}
  .card-back .brand-name{font-size:22px}
  .card-back .brand-mark{width:22px;height:22px}
  .person{position:absolute;right:30px;top:34px;text-align:right}
  .person-name{font-size:15px;font-weight:400;letter-spacing:1.5px;text-transform:uppercase}
  .person-role{font-size:10px;color:var(--ink-soft);margin-top:2px}
  .address{position:absolute;right:30px;top:98px;text-align:right;font-size:11px;line-height:1.7;color:var(--ink)}
  .contacts{position:absolute;left:44px;bottom:28px;list-style:none;font-size:12px;line-height:1.95}
  .contacts li{display:flex;align-items:center;gap:8px}
  .contacts svg{width:11px;height:11px;fill:var(--ink)}
  .swoosh{position:absolute;left:0;bottom:0;width:100%;height:100%}
  .website{position:absolute;right:30px;bottom:16px;font-size:10px;color:#fff;letter-spacing:1px}
</style>
</head>
<body>
  <section class="card card-front" aria-label="Card front">
    <div class="brand"><span class="brand-mark"></span><span class="brand-name">Kestrelbrook</span></div>
  </section>

  <section class="card card-back" aria-label="Card back">
    <svg class="swoosh" viewBox="0 0 530 303" preserveAspectRatio="none" aria-hidden="true">
      <path d="M190 303 C310 250 430 200 530 150 L530 303 Z" fill="var(--yellow)"/>
      <path d="M215 303 C330 258 440 212 530 166 L530 303 Z" fill="var(--green)"/>
    </svg>
    <div class="brand"><span class="brand-mark"></span><span class="brand-name">Kestrelbrook</span></div>
    <div class="person">
      <p class="person-name">Martin Hale</p>
      <p class="person-role">Managing Director</p>
    </div>
    <p class="address">047 Harrow Lane<br>Westmere Road VKL</p>
    <ul class="contacts">
      <li><svg viewBox="0 0 24 24"><path d="M6.6 10.8a15 15 0 0 0 6.6 6.6l2.2-2.2c.3-.3.7-.4 1-.2 1.1.4 2.3.6 3.6.6.6 0 1 .4 1 1V20c0 .6-.4 1-1 1A17 17 0 0 1 3 4c0-.6.4-1 1-1h3.5c.6 0 1 .4 1 1 0 1.3.2 2.5.6 3.6.1.3 0 .7-.2 1z"/></svg>013 482 7510</li>
      <li><svg viewBox="0 0 24 24"><path d="M7 1h10a2 2 0 0 1 2 2v18a2 2 0 0 1-2 2H7a2 2 0 0 1-2-2V3a2 2 0 0 1 2-2zm0 3v14h10V4z"/></svg>013 482 7510</li>
      <li><svg viewBox="0 0 24 24"><path d="M6 2h9v5H6zM3 8h18v10h-3v4H6v-4H3zm5 7v5h8v-5z"/></svg>013 482 7510</li>
      <li><svg viewBox="0 0 24 24"><path d="M2 5h20v14H2zm2 2v.5l8 5 8-5V7z"/></svg>hello@kestrelbrook.com</li>
    </ul>
    <p class="website">www.kestrelbrook.com</p>
  </section>
</body>
</html>
```